Stationery Design Project

Fire and building compliance company needs business card, letterhead and complement slip designed.
Have included a brief about business card, basic want front keep quite clean with just the KTV logo and the words Marlowby Alarm and Guard 2012 Ltd (small print) along the bottom. Website needs to be included (www.ktvalarm.example.nz) on either front or back.
The info for back is as per attachment.
Letterhead and complement slip should have the usual stuff KTV logo etc and also the accredited test lab logo at the bottom (can be small size)
Target Market(s)
Property owners, buisness managers
Industry/Entity Type
Building
Look and feel
Each slider illustrates characteristics of the customer's brand and the style your logo design should communicate.

```html
<!DOCTYPE html>
<html lang="en">
<head>
<meta charset="utf-8">
<title>KTV Business Card</title>
<link href="https://fonts.googleapis.com/css2?family=Montserrat:wght@300;400;600&display=swap" rel="stylesheet">
<style>
  :root {
    --bg: #e9e7e3;
    --card-dark: #2a2a2a;
    --card-light: #f4f4f4;
    --text-light: #f2f2f2;
    --text-dark: #3a3a3a;
    --label-blue: #1f4d6b;
    --rule-blue: #3aa2d6;
    --bullet-red: #d8321e;
    --brand-orange: #e8592a;
  }
  * { box-sizing: border-box; margin: 0; padding: 0; }
  html, body { width: 1200px; height: 900px; overflow: hidden; }
  body {
    background: var(--bg);
    font-family: "Montserrat", sans-serif;
    font-weight: 300;
    position: relative;
  }
  .card {
    position: absolute;
    left: 300px;
    width: 600px;
    height: 340px;
    overflow: hidden;
    box-shadow: 0 6px 18px rgba(0,0,0,0.18);
  }
  .card-front {
    top: 70px;
    background: var(--card-dark);
    color: var(--text-light);
  }
  .brand {
    position: absolute;
    left: 0; right: 0; top: 96px;
    display: flex;
    justify-content: center;
    align-items: center;
    gap: 18px;
  }
  .brand-dot {
    width: 42px; height: 42px;
    border-radius: 50%;
    background: var(--brand-orange);
  }
  .brand-name {
    font-weight: 600;
    font-size: 66px;
    letter-spacing: 2px;
    color: var(--text-light);
  }
  .front-footer {
    position: absolute;
    left: 0; right: 0; bottom: 42px;
    text-align: center;
    font-size: 18px;
    line-height: 1.4;
    letter-spacing: 0.5px;
  }
  .card-back {
    top: 480px;
    display: flex;
  }
  .services {
    width: 47%;
    background: var(--card-dark);
    color: var(--text-light);
    padding: 34px 16px 0 24px;
    list-style: none;
    font-size: 15px;
    line-height: 1.3;
  }
  .services li { position: relative; padding-left: 12px; margin-bottom: 2px; }
  .services li::before {
    content: "";
    position: absolute;
    left: 0; top: 7px;
    width: 4px; height: 4px;
    border-radius: 50%;
    background: var(--bullet-red);
  }
  .contact {
    width: 53%;
    background: var(--card-light);
    color: var(--text-dark);
    padding: 48px 14px 0 22px;
  }
  .person-name {
    font-size: 21px;
    font-weight: 400;
    letter-spacing: 1.5px;
    white-space: nowrap;
    padding-bottom: 16px;
    border-bottom: 1px solid var(--rule-blue);
  }
  .details {
    display: grid;
    grid-template-columns: 64px 1fr;
    font-size: 14px;
    line-height: 1.3;
    padding: 14px 0 16px;
    border-bottom: 1px solid var(--rule-blue);
  }
  .details dt { color: var(--label-blue); font-weight: 400; }
  .details dd { font-size: 13px; white-space: nowrap; }
  .address {
    font-style: normal;
    font-size: 14px;
    line-height: 1.25;
    padding-top: 16px;
  }
</style>
</head>
<body>
  <section class="card card-front">
    <div class="brand">
      <span class="brand-dot"></span>
      <span class="brand-name">KTV</span>
    </div>
    <p class="front-footer">• Marlowby alarm and guard 2012 •<br>www.ktvalarm.example.nz</p>
  </section>

  <section class="card card-back">
    <ul class="services">
      <li>Building compliance specialists</li>
      <li>Building warrant of fitness preparation</li>
      <li>Fire alarms, Fire Extinguishers &amp;emergency lighting</li>
      <li>Approved evacuation schemes</li>
      <li>Pressure testing LPG CNG Fire extinguishers</li>
      <li>Security alarm and CCTV systems</li>
    </ul>
    <div class="contact">
      <h1 class="person-name">RENATA HOLLOWAY</h1>
      <dl class="details">
        <dt>phone</dt><dd>06 555 0148</dd>
        <dt>fax</dt><dd>06 555 0193</dd>
        <dt>email</dt><dd>office@ktvalarm.example.nz</dd>
      </dl>
      <address class="address">Marlowby Alarm and Guard,<br>18 Kestrel Lane,<br>Harrowdene, 4599</address>
    </div>
  </section>
</body>
</html>
```